Dultavo.com webside

I want to build a Dultavo.com retail website use on Shopify, reselling three main categories: Office Supplies, Packing Supplies, and Home Consumables. I also wish the webpage has the same functions as the Zelvik home page. The page is split into three different parts with the top being a sliding screen showcasing promotion products, below it being the three categories, and finally, a moving screen showing company missions.
Target Market(s)
U.S online
Industry/Entity Type
Office Supplies, packing Supplies and Home Consumables
Coding
Coded - Design and coding required
Number of Pages Required
5+ page
Look and feel

```html
<!DOCTYPE html>
<html lang="en">
<head>
<meta charset="utf-8">
<title>Dultavo — Office, Packing &amp; Home Supplies</title>
<link href="https://fonts.googleapis.com/css2?family=Tinos&family=Sarabun:ital,wght@0,400;0,500;0,700;1,400&display=swap" rel="stylesheet">
<style>
:root{
  --bg:#effcf8;
  --brand:#1a9c78;
  --brand-dark:#158566;
  --ink:#222;
  --muted:#666;
  --line:#d6e6e0;
  --card:#ffffff;
}
*{box-sizing:border-box;margin:0;padding:0}
html,body{width:1200px;height:4508px;overflow:hidden}
body{background:var(--bg);font-family:"Sarabun",sans-serif;color:var(--ink);position:relative}
.abs{position:absolute}
.serif{font-family:"Tinos",serif;font-weight:400}
.section-title{position:absolute;font-family:"Tinos",serif;font-size:35px;color:#222;letter-spacing:.5px;line-height:1}
.center{left:0;width:1200px;text-align:center}

/* header */
.site-header{position:absolute;left:0;top:0;width:1200px;height:142px;background:var(--bg)}
.logo{position:absolute;left:0;width:1200px;top:24px;text-align:center;font-family:"Tinos",serif;font-size:31px;color:var(--brand);letter-spacing:1px}
.main-nav{position:absolute;top:91px;left:0;width:1200px;text-align:center;font-size:13px;letter-spacing:.4px;color:#333}
.main-nav span{padding:0 10px}
.main-nav .sep{padding:0;color:#555}
.main-nav .active{color:var(--brand)}

/* hero */
.hero{position:absolute;left:0;top:142px;width:1200px;height:556px;background:linear-gradient(100deg,#b9b6b1 0%,#d6d2cc 35%,#cfc9c1 60%,#a7a199 100%)}
.hero-title{position:absolute;left:108px;top:150px;font-family:"Tinos",serif;font-size:70px;line-height:76px;color:#fff;letter-spacing:1px}
.btn-shop{position:absolute;left:114px;top:316px;width:143px;height:44px;background:var(--brand);color:#fff;font-family:"Tinos",serif;font-size:14px;display:flex;align-items:center;justify-content:center;letter-spacing:.5px}
.offer{position:absolute;left:816px;top:54px;width:168px;height:168px}
.offer-text{position:absolute;left:816px;top:84px;width:168px;text-align:center;color:#fff;font-family:"Tinos",serif;font-size:29px;line-height:33px}
.offer-text b{font-family:"Sarabun",sans-serif;font-weight:700;font-size:28px;display:block;margin-top:4px}
.dots{position:absolute;left:574px;top:503px;display:flex;gap:4px}
.dots i{width:12px;height:12px;border-radius:50%;background:#fff;display:block}
.dots i.on{background:var(--brand)}

/* cards */
.card{position:absolute;background:var(--card);border:1px solid var(--line);border-radius:4px;overflow:hidden}
.ph{position:absolute;left:0;top:0;width:100%}
.card-label{position:absolute;font-size:21px;color:#333;display:flex;align-items:center;gap:14px}
.card-label svg{width:34px;height:14px}

/* testimonials */
.quote{position:absolute;top:2042px;width:320px;text-align:center;font-style:italic;font-size:13.5px;line-height:26px;color:#333}
.q-name{position:absolute;top:2212px;width:320px;text-align:center;font-weight:700;font-size:18px}
.q-co{position:absolute;top:2242px;width:320px;text-align:center;font-size:13px;color:#555}

/* features */
.feature{position:absolute;top:3040px;width:230px;text-align:center}
.feature .ico{width:84px;height:84px;border-radius:50%;background:var(--brand);margin:0 auto;display:flex;align-items:center;justify-content:center}
.feature h3{font-size:19px;font-weight:700;margin-top:16px}
.feature p{font-size:13px;line-height:26px;color:#555;margin-top:12px}

/* blog */
.post h3{position:absolute;left:21px;top:228px;font-size:19px;font-weight:700}
.post .date{position:absolute;left:21px;top:270px;font-size:13.5px;color:var(--brand);display:flex;align-items:center;gap:4px}
.post p{position:absolute;left:21px;top:304px;width:270px;font-size:13px;line-height:26px;color:#555}

/* footer */
.site-footer{position:absolute;left:0;top:3931px;width:1200px;height:577px;background:var(--brand);color:#fff}
.newsletter-title{position:absolute;top:90px;font-family:"Tinos",serif;font-size:35px}
.newsletter-sub{position:absolute;top:142px;font-size:13px}
.email{position:absolute;left:332px;top:182px;width:536px;height:57px;border:2px solid #fff;border-radius:6px;font-size:14px;display:flex;align-items:center;justify-content:space-between;padding:0 20px}
.f-title{position:absolute;top:290px;font-family:"Tinos",serif;font-size:22px;letter-spacing:.5px}
.f-link{position:absolute;font-size:13px}
.f-text{position:absolute;left:653px;top:334px;font-size:13px;line-height:26px}
.f-rule{position:absolute;left:0;top:447px;width:1200px;height:1px;background:rgba(255,255,255,.35)}
.copy{position:absolute;top:470px;font-size:13px}
.pay{position:absolute;top:511px;left:425px;display:flex;gap:15px}
.pay i{display:block;width:45px;height:26px;background:#fff;border-radius:4px}
</style>
</head>
<body>

<header class="site-header">
  <svg class="abs" style="left:307px;top:32px" width="16" height="16" viewBox="0 0 16 16"><circle cx="6.5" cy="6.5" r="4.5" fill="none" stroke="#222" stroke-width="2"/><line x1="10" y1="10" x2="14" y2="14" stroke="#222" stroke-width="2.4" stroke-linecap="round"/></svg>
  <div class="logo">DULTAVO</div>
  <svg class="abs" style="left:876px;top:32px" width="16" height="15" viewBox="0 0 16 15"><path d="M1 1h3l2 8h8l2-6H5" fill="none" stroke="#222" stroke-width="2"/><path d="M5 3h10l-1.5 6H6z" fill="#222"/><circle cx="7" cy="12.5" r="1.5" fill="#222"/><circle cx="13" cy="12.5" r="1.5" fill="#222"/></svg>
  <nav class="main-nav">
    <span class="active">HOME</span><span class="sep">|</span><span>ABOUT</span><span class="sep">|</span><span>PRODUCTS</span><span class="sep">|</span><span>SERVICES</span><span class="sep">|</span><span>BLOG</span><span class="sep">|</span><span>REVIEWS</span><span class="sep">|</span><span>CONTACT</span>
  </nav>
</header>

<section class="hero" role="img" aria-label="Bright home office with a desk, computer, chair, shelves and a potted plant">
  <h1 class="hero-title serif">OFFICE<br>SUPPLIES</h1>
  <div class="btn-shop">SHOP NOW</div>
  <svg class="offer" viewBox="0 0 168 168">
    <path fill="var(--brand)" d="M84 2 L96 12 L111 7 L119 21 L135 22 L137 38 L151 46 L146 61 L157 73 L147 85 L153 100 L139 108 L138 124 L122 127 L115 141 L100 137 L88 148 L76 139 L61 145 L52 132 L36 132 L33 116 L19 108 L24 93 L14 81 L25 69 L20 54 L34 47 L36 31 L52 29 L60 16 L75 20 Z" transform="translate(0 10)"/>
  </svg>
  <div class="offer-text">SPECIAL<br>OFFER<b>25%</b></div>
  <div class="dots"><i></i><i class="on"></i><i></i></div>
</section>

<h2 class="section-title center" style="top:790px">OUR MAIN CATEGORIES</h2>

<div class="card" style="left:110px;top:859px;width:311px;height:413px">
  <div class="ph" style="height:334px;background:linear-gradient(135deg,#d9d4cc,#e8c6a8 40%,#b9d3e6 70%,#ddd8d0)" role="img" aria-label="Colourful pens, paper clips, sticky notes and scissors"></div>
  <div class="card-label" style="left:21px;top:360px">Office Supplies <svg viewBox="0 0 34 14"><path d="M0 7h31M25 1l7 6-7 6" fill="none" stroke="var(--brand)" stroke-width="2.2"/></svg></div>
</div>
<div class="card" style="left:444px;top:859px;width:312px;height:413px">
  <div class="ph" style="height:334px;background:linear-gradient(135deg,#c9b79b,#a88e6a 50%,#d8cdbd)" role="img" aria-label="Tape dispenser sealing a cardboard box"></div>
  <div class="card-label" style="left:21px;top:360px">Packing Supplies <svg viewBox="0 0 34 14"><path d="M0 7h31M25 1l7 6-7 6" fill="none" stroke="var(--brand)" stroke-width="2.2"/></svg></div>
</div>
<div class="card" style="left:779px;top:859px;width:311px;height:413px">
  <div class="ph" style="height:334px;background:linear-gradient(135deg,#9fb4c9,#6f8fb0 40%,#c9a06a 70%,#b44a5a)" role="img" aria-label="Shopper holding a bag full of fresh groceries"></div>
  <div class="card-label" style="left:21px;top:360px">Home Consumables <svg viewBox="0 0 34 14"><path d="M0 7h31M25 1l7 6-7 6" fill="none" stroke="var(--brand)" stroke-width="2.2"/></svg></div>
</div>

<h2 class="section-title" style="left:110px;top:1368px">OUR MISSIONS</h2>
<div class="abs" style="left:110px;top:1426px;width:979px;height:452px;border-radius:6px;background:linear-gradient(100deg,#5d6a78,#8a8f8a 30%,#c4b89f 55%,#a09886 80%,#6a7180)" role="img" aria-label="Cardboard boxes moving along a warehouse conveyor">
  <svg class="abs" style="left:468px;top:205px" width="42" height="42" viewBox="0 0 42 42"><circle cx="21" cy="21" r="21" fill="#fff"/><path d="M16 12l14 9-14 9z" fill="#222"/></svg>
</div>

<h2 class="section-title center" style="top:1975px">OUR CUSTOMERS SAY</h2>
<p class="quote" style="left:94px">“Lorem ipsum dolor sit amet, cons ectetur adipiscing elit, sed do eiusmod tempor incidid unt ut labore et dolore magna aliqua. Ut enim ad minim veniam, quis nostrud exercitation ullamco laboris nisi ut aliquip ex ea commodo consequat.”</p>
<p class="quote" style="left:435px">“Lorem ipsum dolor sit amet, cons ectetur adipiscing elit, sed do eiusmod tempor incidid unt ut labore et dolore magna aliqua. Ut enim ad minim veniam, quis nostrud exercitation ullamco laboris nisi ut aliquip ex ea commodo consequat.”</p>
<p class="quote" style="left:775px">“Lorem ipsum dolor sit amet, cons ectetur adipiscing elit, sed do eiusmod tempor incidid unt ut labore et dolore magna aliqua. Ut enim ad minim veniam, quis nostrud exercitation ullamco laboris nisi ut aliquip ex ea commodo consequat.”</p>
<div class="q-name" style="left:94px">John Doe</div><div class="q-co" style="left:94px">Company name</div>
<div class="q-name" style="left:435px">John Doe</div><div class="q-co" style="left:435px">Company name</div>
<div class="q-name" style="left:775px">John Doe</div><div class="q-co" style="left:775px">Company name</div>

<h2 class="section-title" style="left:110px;top:2366px">OUR PRODUCTS</h2>
<div class="card" style="left:110px;top:2429px;width:582px;height:508px">
  <div class="ph" style="height:411px;background:linear-gradient(135deg,#e6e2dc,#d9cfc2 40%,#e3a86a 65%,#cfd6d4)" role="img" aria-label="Flat lay of pens, pencils, highlighters, clips and an ID badge"></div>
  <div class="card-label" style="left:21px;top:440px">Product 1 <svg viewBox="0 0 34 14"><path d="M0 7h31M25 1l7 6-7 6" fill="none" stroke="var(--brand)" stroke-width="2.2"/></svg></div>
</div>
<div class="card" style="left:712px;top:2429px;width:377px;height:242px;background:linear-gradient(135deg,#eceae6,#d4cfc6 50%,#b88a5e)" role="img" aria-label="Office with desk, chairs and moving boxes"></div>
<div class="card" style="left:712px;top:2697px;width:377px;height:240px;background:linear-gradient(135deg,#f2f0ec,#e4e2dc 50%,#c9b06a 75%,#7aa36a)" role="img" aria-label="Paper towel rolls and fresh produce on a kitchen counter"></div>

<div class="feature" style="left:100px">
  <div class="ico"><svg width="44" height="44" viewBox="0 0 44 44" fill="none" stroke="#fff" stroke-width="2"><circle cx="22" cy="17" r="12"/><path d="M17 17l4 4 7-8M15 27l-4 12 6-3 3 5 2-10M29 27l4 12-6-3-3 5"/></svg></div>
  <h3>Consequuntur</h3><p>Lorem ipsum dolor sit amet, co nsectetur adipiscing elit, sed do eiusmod tempor incid</p>
</div>
<div class="feature" style="left:357px">
  <div class="ico"><svg width="46" height="40" viewBox="0 0 46 40" fill="none" stroke="#fff" stroke-width="2"><path d="M2 12l8-4 8 4 6-3 6 3 8-4 6 4M6 14l10 12 6 4 6-4 10-12M16 26l4-4M22 30l4-4M28 26l-6-6"/></svg></div>
  <h3>Consequuntur</h3><p>Lorem ipsum dolor sit amet, co nsectetur adipiscing elit, sed do eiusmod tempor incid</p>
</div>
<div class="feature" style="left:611px">
  <div class="ico"><svg width="42" height="42" viewBox="0 0 42 42" fill="none" stroke="#fff" stroke-width="2"><path d="M21 4l16 8v18l-16 8-16-8V12zM5 12l16 8 16-8M21 20v18M13 8l16 8"/></svg></div>
  <h3>Consequuntur</h3><p>Lorem ipsum dolor sit amet, co nsectetur adipiscing elit, sed do eiusmod tempor incid</p>
</div>
<div class="feature" style="left:868px">
  <div class="ico"><svg width="48" height="36" viewBox="0 0 48 36" fill="none" stroke="#fff" stroke-width="2"><path d="M8 6h22v20H8zM30 12h8l6 7v7h-14zM4 12h8M2 18h8"/><circle cx="14" cy="28" r="4"/><circle cx="37" cy="28" r="4"/></svg></div>
  <h3>Consequuntur</h3><p>Lorem ipsum dolor sit amet, co nsectetur adipiscing elit, sed do eiusmod tempor incid</p>
</div>

<h2 class="section-title" style="left:110px;top:3346px">FROM THE BLOG</h2>
<article class="card post" style="left:110px;top:3416px;width:311px;height:413px">
  <div class="ph" style="height:207px;background:linear-gradient(135deg,#5b7a4a,#9fb08a 40%,#c9453a 65%,#e6d9b8)" role="img" aria-label="Basket of fresh vegetables being handed over"></div>
  <h3>Consequuntur</h3>
  <div class="date"><svg width="12" height="12" viewBox="0 0 12 12"><rect x="1" y="2" width="10" height="9" fill="none" stroke="var(--brand)" stroke-width="1.5"/><path d="M1 5h10M4 1v2M8 1v2" stroke="var(--brand)" stroke-width="1.5"/></svg>Jan 20,2022</div>
  <p>Lorem ipsum dolor sit amet, co nsecte tur adipiscing elit, sed do eiusmod te mpor incid</p>
</article>
<article class="card post" style="left:444px;top:3416px;width:312px;height:413px">
  <div class="ph" style="height:207px;background:linear-gradient(135deg,#3f4448,#6b6e70 40%,#b08a5e 70%,#8a8680)" role="img" aria-label="Stacked moving boxes in an empty office"></div>
  <h3>Consequuntur</h3>
  <div class="date"><svg width="12" height="12" viewBox="0 0 12 12"><rect x="1" y="2" width="10" height="9" fill="none" stroke="var(--brand)" stroke-width="1.5"/><path d="M1 5h10M4 1v2M8 1v2" stroke="var(--brand)" stroke-width="1.5"/></svg>Jan 20,2022</div>
  <p>Lorem ipsum dolor sit amet, co nsecte tur adipiscing elit, sed do eiusmod te mpor incid</p>
</article>
<article class="card post" style="left:779px;top:3416px;width:311px;height:413px">
  <div class="ph" style="height:207px;background:linear-gradient(135deg,#d8d6d2,#c9a88a 45%,#b07c4e 75%,#8a5a3a)" role="img" aria-label="Shop owner checking orders beside parcel boxes"></div>
  <h3>Consequuntur</h3>
  <div class="date"><svg width="12" height="12" viewBox="0 0 12 12"><rect x="1" y="2" width="10" height="9" fill="none" stroke="var(--brand)" stroke-width="1.5"/><path d="M1 5h10M4 1v2M8 1v2" stroke="var(--brand)" stroke-width="1.5"/></svg>Jan 20,2022</div>
  <p>Lorem ipsum dolor sit amet, co nsecte tur adipiscing elit, sed do eiusmod te mpor incid</p>
</article>

<footer class="site-footer">
  <h2 class="newsletter-title center">DON'T MISS OUT</h2>
  <p class="newsletter-sub center">Subscribe to our mailing list for insider news, product launches, and more.</p>
  <div class="email"><span>Email address</span><svg width="22" height="12" viewBox="0 0 22 12"><path d="M0 6h20M15 1l5 5-5 5" fill="none" stroke="#fff" stroke-width="2"/></svg></div>
  <h3 class="f-title" style="left:233px">GET TO KNOW DULTAVO</h3>
  <div class="f-link" style="left:233px;top:337px">About</div>
  <div class="f-link" style="left:233px;top:372px">Magazine</div>
  <h3 class="f-title" style="left:653px">OUR MISSION</h3>
  <p class="f-text">Lorem ipsum dolor sit amet, consectetur adipisc<br>ing elit, sed do eiusmod tempor incididunt<br>ut labore et dolore magna aliqua.</p>
  <div class="f-rule"></div>
  <p class="copy center">Copyright 2022 Company name | All Rights Reserved</p>
  <div class="pay" aria-label="Accepted payment methods"><i></i><i></i><i></i><i></i><i></i><i></i></div>
</footer>

</body>
</html>
```